New Business Card Design Project

We are a spa looking to create a professional elegant business card for a spa mainly black and white with a splash of lime green. This card will be two sided - the front side will have an image, the logo, and the spa's information - the back side will have a promotion for new customers - NEW CUSTOMERS $20 OFF

Look and feel: chic, modern, and spa-ish.
Information to be included:
Therapist Name
Therapist specialty
Address: 4719 Marlowe Ave, Beverly Hills CA 90211
Phone: (310) 482-3917

Let me know if you have any questions!

Thank you

```html
<!DOCTYPE html>
<html lang="en">
<head>
<meta charset="utf-8">
<title>Lumen Day Spa – Business Card</title>
<link rel="stylesheet" href="https://fonts.googleapis.com/css2?family=Great+Vibes&family=Lora:ital,wght@0,400;0,600;1,400&family=Montserrat:wght@400&display=swap">
<style>
  :root {
    --backdrop: #e9e7e3;
    --card: #f7f7f6;
    --ink: #161616;
    --ink-soft: #3a3a3a;
    --lime: #7cc242;
    --pattern-dark: #1c1c1c;
    --pattern-light: #d9d9d9;
  }
  * { box-sizing: border-box; margin: 0; padding: 0; }
  html, body { width: 1200px; height: 723px; overflow: hidden; }
  body {
    background: var(--backdrop);
    display: flex;
    align-items: center;
    justify-content: center;
    gap: 70px;
    font-family: "Lora", Georgia, serif;
    color: var(--ink);
  }
  .card {
    width: 360px;
    height: 630px;
    background: var(--card);
    position: relative;
    display: flex;
    flex-direction: column;
    align-items: center;
    box-shadow: 0 6px 18px rgba(0,0,0,.18);
  }
  .damask-band {
    width: 100%;
    height: 96px;
    background: linear-gradient(180deg, var(--pattern-dark) 0%, #4a4a4a 50%, var(--pattern-dark) 100%);
    flex: none;
  }
  .brand {
    display: flex;
    flex-direction: column;
    align-items: center;
    gap: 14px;
    margin-top: 34px;
  }
  .brand-dot {
    width: 22px; height: 22px;
    border-radius: 50%;
    background: var(--ink);
  }
  .brand-name {
    font-family: "Lora", Georgia, serif;
    font-weight: 400;
    font-size: 30px;
    letter-spacing: 3px;
    text-transform: uppercase;
    color: var(--ink);
  }
  .therapist {
    margin-top: 26px;
    text-align: center;
  }
  .therapist-name {
    font-family: "Great Vibes", cursive;
    font-size: 48px;
    line-height: 1;
    color: var(--ink);
  }
  .therapist-role {
    font-family: "Montserrat", sans-serif;
    font-size: 20px;
    letter-spacing: 7px;
    color: var(--lime);
    margin-top: 2px;
  }
  .contact {
    margin-top: 24px;
    width: 280px;
    font-size: 17px;
    line-height: 1.35;
  }
  .contact-row { display: flex; gap: 8px; align-items: baseline; }
  .contact-label {
    font-style: italic;
    font-size: 11px;
    color: var(--lime);
    width: 50px;
    text-align: right;
    flex: none;
  }
  .contact-value { font-weight: 600; }
  .contact-row + .contact-row { margin-top: 4px; }
  .spacer { flex: 1; }
  .promo {
    margin-top: 70px;
    font-size: 22px;
    letter-spacing: 1px;
    text-transform: uppercase;
    color: var(--ink-soft);
    text-align: center;
  }
  .promo-amount { color: var(--lime); }
</style>
</head>
<body>
  <section class="card card-front">
    <div class="damask-band" role="img" aria-label="Black and white damask pattern band"></div>
    <div class="brand">
      <span class="brand-dot"></span>
      <span class="brand-name">Lumen Day Spa</span>
    </div>
    <div class="therapist">
      <div class="therapist-name">John Doe</div>
      <div class="therapist-role">therapist</div>
    </div>
    <div class="contact">
      <div class="contact-row">
        <span class="contact-label">address</span>
        <span class="contact-value">4719 Marlowe Ave<br>Beverly Hills CA 90211</span>
      </div>
      <div class="contact-row">
        <span class="contact-label">phone</span>
        <span class="contact-value">(310) 482-3917</span>
      </div>
    </div>
    <div class="spacer"></div>
    <div class="damask-band" role="img" aria-label="Black and white damask pattern band"></div>
  </section>

  <section class="card card-back">
    <div class="damask-band" role="img" aria-label="Black and white damask pattern band"></div>
    <div class="brand" style="margin-top:70px">
      <span class="brand-dot"></span>
      <span class="brand-name">Lumen Day Spa</span>
    </div>
    <p class="promo">New Customers <span class="promo-amount">$20 Off</span></p>
    <div class="spacer"></div>
    <div class="damask-band" role="img" aria-label="Black and white damask pattern band"></div>
  </section>
</body>
</html>
```